Veldmark Supplies Business Card

Professional business card that stand out to our potential customers. Front and back with clean modern design

Industry/Entity Type

Oil and gas

Contact Information for Business Card

Name, address, website , office phone and cell number

Requirements
Must have
• Editable files for each employee

```html
<!DOCTYPE html>
<html lang="en">
<head>
<meta charset="utf-8">
<title>Veldmark Supplies Business Card</title>
<link href="https://fonts.googleapis.com/css2?family=Montserrat:wght@400;500;700&display=swap" rel="stylesheet">
<style>
  :root {
    --bg: #3a3a3c;
    --card-white: #ffffff;
    --card-dark: #1c1c1c;
    --red: #f20d0d;
    --blue: #05aed0;
    --ink: #1a1a1a;
    --light: #f4f4f4;
  }
  * { margin: 0; padding: 0; box-sizing: border-box; }
  html, body { width: 1200px; height: 1200px; overflow: hidden; }
  body {
    background: var(--bg);
    font-family: "Montserrat", sans-serif;
    display: flex;
    flex-direction: column;
    align-items: center;
    justify-content: center;
    gap: 40px;
  }
  .card {
    position: relative;
    width: 980px;
    height: 540px;
    border-radius: 40px;
    overflow: hidden;
    box-shadow: 0 14px 30px rgba(0,0,0,.45);
  }
  .card-front { background: var(--card-white); }
  .card-back { background: var(--card-dark); border-bottom: 4px solid var(--red); }

  .front-bands { position: absolute; left: 0; bottom: 0; width: 100%; height: 160px; }

  .contact-block {
    position: absolute;
    left: 90px;
    top: 250px;
    color: var(--ink);
  }
  .full-name {
    font-weight: 700;
    font-size: 50px;
    color: var(--red);
    letter-spacing: 1px;
    line-height: 1;
  }
  .job-title {
    font-weight: 400;
    font-size: 30px;
    letter-spacing: 2px;
    margin: 4px 0 18px 2px;
  }
  .contact-list { list-style: none; }
  .contact-list li {
    display: flex;
    align-items: flex-start;
    gap: 16px;
    font-size: 24px;
    line-height: 30px;
    margin-bottom: 2px;
  }
  .contact-list svg { width: 22px; height: 26px; flex: none; margin-top: 2px; }

  .brand {
    position: absolute;
    display: flex;
    align-items: center;
    gap: 16px;
    font-weight: 700;
    letter-spacing: 2px;
    white-space: nowrap;
  }
  .brand-square { display: block; background: var(--blue); flex: none; }
  .card-front .brand { right: 90px; top: 150px; font-size: 40px; color: var(--red); }
  .card-front .brand-square { width: 44px; height: 44px; }
  .card-back .brand {
    left: 50%; top: 200px; transform: translateX(-50%);
    font-size: 52px; color: var(--red);
  }
  .card-back .brand-square { width: 56px; height: 56px; }

  .website {
    position: absolute;
    left: 0; right: 0;
    top: 320px;
    text-align: center;
    color: var(--light);
    font-size: 30px;
    font-weight: 400;
    letter-spacing: 2px;
  }
</style>
</head>
<body>

  <section class="card card-front">
    <div class="brand"><span class="brand-square"></span>VELDMARK SUPPLIES</div>

    <div class="contact-block">
      <h1 class="full-name">FULL NAME</h1>
      <p class="job-title">TITLE</p>
      <ul class="contact-list">
        <li>
          <svg viewBox="0 0 22 26" aria-hidden="true"><rect x="4" y="1" width="14" height="24" rx="2" fill="none" stroke="var(--red)" stroke-width="2"/><line x1="9" y1="21" x2="13" y2="21" stroke="var(--red)" stroke-width="2"/></svg>
          (000) 000 0000
        </li>
        <li>
          <svg viewBox="0 0 22 26" aria-hidden="true"><path d="M4 3 L9 3 L10 9 L7 11 C8 15 11 18 15 19 L17 16 L21 17 L21 22 C12 23 3 14 4 3 Z" fill="var(--red)"/></svg>
          (000) 000 0000
        </li>
        <li>
          <svg viewBox="0 0 22 26" aria-hidden="true"><rect x="1" y="6" width="20" height="14" fill="var(--red)"/><polyline points="1,6 11,14 21,6" fill="none" stroke="#fff" stroke-width="1.6"/></svg>
          email@company.com
        </li>
        <li>
          <svg viewBox="0 0 22 26" aria-hidden="true"><path d="M11 25 C5 17 2 13 2 9 A9 9 0 0 1 20 9 C20 13 17 17 11 25 Z" fill="var(--red)"/><circle cx="11" cy="9" r="3.5" fill="#fff"/></svg>
          <span>123 Name Street, 000<br>Your City, 00000-000</span>
        </li>
      </ul>
    </div>

    <svg class="front-bands" viewBox="0 0 980 160" preserveAspectRatio="none" aria-hidden="true">
      <polygon points="0,135 600,135 590,160 0,160" fill="var(--red)"/>
      <polygon points="612,95 980,95 980,160 600,160" fill="var(--blue)"/>
    </svg>
  </section>

  <section class="card card-back">
    <div class="brand"><span class="brand-square"></span>VELDMARK SUPPLIES</div>
    <p class="website">WWW.COMPANY.COM</p>
  </section>

</body>
</html>
```